4D Cradle Glimpse Luxury Ultrasound Billboard

Design a HIGH-END, MODERN billboard for my private prenatal ultrasound studio, 4D Cradle Glimpse, located in Pace, Florida.
This billboard will be viewed by drivers traveling at highway speeds, so it must be extremely clean, simple, and readable within 6 seconds.
About My Business
4D Cradle Glimpse is a private prenatal ultrasound studio specializing in:
Highest technology 4D/HD Ultrasounds
Early Gender Determination
Pregnancy Confirmation
I have been serving families for nearly 10 years and is known for creating a memorable experience, not just an ultrasound appointment.
Design Style
I DO NOT want:
Flowers
Leaves
Swirls
Glitter
Hearts everywhere
Busy backgrounds
Generic maternity stock graphics
I DO want:
Modern
Luxury
Upscale
Clean
Professional
Eye-catching
Premium medical spa feel
Colors
Use colors from my logo:
LOGO Green ( or a deep green)
Black
White
Soft Gold accents
Images:
Incorporate my professional headshot in a clean, modern way, logo, and the ultrasound images
Text
Keep wording minimal.
Primary Headline ( OPEN TO IDEAS) :
EXAMPLES ( WOULD RATHER SOMETHING MORE CATCHY)
" ADVANCED IMAGING. UNFORGETTABLE MOMENTS"
"MEET YOUR BABY BEFORE BIRTH"
Under headline:
4D Ultrasound • Early Gender • Pregnancy Confirmation
Business Name:
4D Cradle Glimpse
Private Prenatal Ultrasound Studio
Phone Number:
850-471-5923
Important
This billboard must be readable in 5–6 seconds from a moving vehicle.
Less text is better.
The phone number and business name must be visible from a distance.
The design should feel like a premium brand that immediately tells expecting parents:
“This is where I go to see my baby.”
Files Provided
Official logo
Headshot
Ultrasound images
Don’t make this look like a medical office billboard.
Make it look like a luxury baby experience billboard. That’s what separates 4D Cradle Glimpse from hospitals, OB offices, and all the new studios popping up around you. The emotional connection is what gets moms to book. ❤️
Billboard Size - 10.6” x 36”

```html
<!DOCTYPE html>
<html lang="en">
<head>
<meta charset="utf-8">
<title>4D Cradle Glimpse Billboard</title>
<link rel="stylesheet" href="https://fonts.googleapis.com/css2?family=Libre+Baskerville:wght@400;700&family=Montserrat:wght@500;600&family=Open+Sans:wght@700&family=Great+Vibes&display=swap">
<style>
  :root {
    --page: #7a818a;
    --cream: #f8f6f1;
    --green: #3f5048;
    --green-ink: #3b4a43;
    --gold: #c0953d;
    --white: #ffffff;
  }
  html, body {
    margin: 0;
    width: 1145px;
    height: 1200px;
    overflow: hidden;
    background: var(--page);
  }
  .billboard {
    position: absolute;
    left: 30px;
    top: 435px;
    width: 1085px;
    height: 329px;
    display: block;
    box-shadow: 0 10px 22px rgba(0,0,0,.35);
  }
  .headline { font-family: "Libre Baskerville", Georgia, serif; font-weight: 700; }
  .headline--dark { fill: var(--green-ink); }
  .headline--gold { fill: var(--gold); }
  .services { font-family: "Montserrat", Arial, sans-serif; font-weight: 500; font-size: 14.5px; fill: var(--green-ink); }
  .phone-number { font-family: "Open Sans", Arial, sans-serif; font-weight: 700; fill: var(--white); }
  .brand-name { font-family: "Libre Baskerville", Georgia, serif; font-weight: 700; fill: var(--green-ink); }
  .brand-descriptor { font-family: "Montserrat", Arial, sans-serif; font-weight: 600; font-size: 9px; fill: var(--green-ink); letter-spacing: .4px; }
  .tagline-script { font-family: "Great Vibes", cursive; font-size: 32px; fill: var(--gold); }
  .tagline-caps { font-family: "Libre Baskerville", Georgia, serif; font-size: 13px; fill: var(--white); letter-spacing: 2px; }
</style>
</head>
<body>
<svg class="billboard" viewBox="0 0 1085 329" xmlns="http://www.w3.org/2000/svg">
  <defs>
    <linearGradient id="scan-tone" x1="0" y1="0" x2="1" y2="0">
      <stop offset="0" stop-color="#f8f6f1"/>
      <stop offset=".12" stop-color="#c98a70"/>
      <stop offset=".45" stop-color="#b0654b"/>
      <stop offset=".55" stop-color="#2a1510"/>
      <stop offset=".68" stop-color="#b8745a"/>
      <stop offset="1" stop-color="#8e4632"/>
    </linearGradient>
    <linearGradient id="portrait-tone" x1="0" y1="0" x2="0" y2="1">
      <stop offset="0" stop-color="#efece6"/>
      <stop offset=".35" stop-color="#d6bf8f"/>
      <stop offset=".7" stop-color="#2f4a3a"/>
      <stop offset="1" stop-color="#e8e6e2"/>
    </linearGradient>
  </defs>

  <rect class="canvas" x="0" y="0" width="1085" height="329" fill="var(--cream)"/>

  <g role="img" aria-label="4D ultrasound image of twin babies face to face">
    <rect x="745" y="0" width="340" height="268" fill="url(#scan-tone)"/>
  </g>

  <rect class="contact-band" x="0" y="268" width="1085" height="61" fill="var(--green)"/>
  <path class="band-swoosh" d="M760 262 C728 275 722 318 696 329" fill="none" stroke="var(--gold)" stroke-width="2"/>

  <g role="img" aria-label="Professional headshot of the studio sonographer">
    <rect x="20" y="120" width="185" height="209" fill="url(#portrait-tone)"/>
  </g>

  <g class="brand-lockup">
    <rect x="17" y="15" width="239" height="101" rx="10" fill="none" stroke="#5a6660" stroke-width="1.5"/>
    <text class="brand-name" x="136.5" y="58" text-anchor="middle" font-size="21" textLength="205" lengthAdjust="spacingAndGlyphs">4D Cradle Glimpse</text>
    <line x1="35" y1="80" x2="238" y2="80" stroke="var(--gold)" stroke-width="1"/>
    <text class="brand-descriptor" x="136.5" y="100" text-anchor="middle">PRENATAL ULTRASOUND STUDIO</text>
  </g>

  <g class="headline-block">
    <text class="headline headline--dark" x="306" y="60" font-size="61" textLength="430" lengthAdjust="spacingAndGlyphs">MEET YOUR</text>
    <text class="headline headline--gold" x="310" y="155" font-size="120" textLength="430" lengthAdjust="spacingAndGlyphs">BABY</text>
    <text class="headline headline--dark" x="310" y="196" font-size="48" textLength="438" lengthAdjust="spacingAndGlyphs">BEFORE BIRTH</text>
  </g>

  <g class="divider">
    <line x1="288" y1="215" x2="510" y2="215" stroke="var(--gold)" stroke-width="1"/>
    <line x1="530" y1="215" x2="775" y2="215" stroke="var(--gold)" stroke-width="1"/>
    <path d="M520 222 L513 215 A3.6 3.6 0 0 1 520 210 A3.6 3.6 0 0 1 527 215 Z" fill="var(--gold)"/>
  </g>

  <text class="services" x="289" y="243" textLength="486" lengthAdjust="spacing">4D Ultrasound   •   Early Gender   •   Pregnancy Confirmation</text>

  <g class="phone">
    <circle cx="295" cy="296" r="26" fill="var(--gold)"/>
    <path d="M285 283 c2-2 5-2 6 0 l3 5 c1 2 0 3-2 4 c1 4 4 7 8 8 c1-2 2-3 4-2 l5 3 c2 1 2 4 0 6 c-3 3-7 3-12 0 c-6-4-10-9-13-15 c-2-4-1-7 1-9z" fill="var(--white)"/>
    <text class="phone-number" x="337" y="312" font-size="48" textLength="341" lengthAdjust="spacingAndGlyphs">850-471-5923</text>
  </g>

  <g class="tagline">
    <text class="tagline-script" x="772" y="297" textLength="239" lengthAdjust="spacingAndGlyphs">Cherished Moments,</text>
    <text class="tagline-caps" x="799" y="314" textLength="178" lengthAdjust="spacing">LAST A LIFETIME.</text>
    <path d="M989 318 L983 312 A3 3 0 0 1 989 307.5 A3 3 0 0 1 995 312 Z" fill="var(--gold)"/>
  </g>
</svg>
</body>
</html>
```